Quillbrookes websites redesign

Www.quill-brookes.com needs to be redesigned along with updations. The incremental material will be provided for the updations. We are looking for complete redesign of the pages with the new content. The complete write up will be provided soon

Target Market(s)

Global

Coding

Coded - Design and coding required

Number of Pages Required

5+ page

Requirements
Must have
• A clean and slick design for the Consulting.
Should not have
• Too many pictures which reduces the speed of the site

```html
<!DOCTYPE html>
<html lang="en">
<head>
<meta charset="utf-8">
<title>Quillbrookes Consultancy</title>
<link rel="stylesheet" href="https://fonts.googleapis.com/css2?family=Raleway:wght@400;500;600;700&family=Open+Sans:wght@400;600;700&display=swap">
<style>
:root{
  --navy:#0b4a82;
  --navy-dark:#07375f;
  --ink:#333;
  --muted:#6b6b6b;
  --line:#e3e3e3;
  --white:#fff;
  --blue:#1a86cf;
  --green:#7fb239;
  --orange:#ee6a1f;
  --red:#bb1c24;
}
*{margin:0;padding:0;box-sizing:border-box}
html,body{width:1200px;height:2486px;overflow:hidden;background:var(--white)}
body{position:relative;font-family:"Open Sans",Arial,sans-serif;color:var(--ink)}
.abs{position:absolute}
.center{text-align:center}

/* header */
.site-header{position:absolute;left:0;top:0;width:1200px;height:71px;background:var(--white)}
.brand{position:absolute;left:103px;top:18px;display:flex;align-items:center;gap:10px;font-family:"Raleway",sans-serif;font-size:30px;font-weight:500;color:#3a2a3a}
.brand-dot{width:28px;height:28px;border-radius:50%;background:var(--navy)}
.main-nav{position:absolute;right:100px;top:30px;display:flex;gap:62px;font-family:"Raleway",sans-serif;font-size:12px;font-weight:600;color:#333;letter-spacing:.2px}

/* hero */
.hero{position:absolute;left:0;top:71px;width:1200px;height:555px;background:radial-gradient(ellipse 95% 70% at 50% 95%,#4d76b3 0%,#1d3c86 30%,#0c1d5a 60%,#070f3b 100%)}
.hero-title{position:absolute;left:0;width:1200px;top:140px;font-family:"Raleway",sans-serif;font-weight:700;font-size:38px;letter-spacing:4px;color:var(--white)}
.hero-sub{position:absolute;left:0;width:1200px;top:197px;font-family:"Raleway",sans-serif;font-weight:400;font-size:22px;letter-spacing:2.5px;color:#e8eefc}
.bubble{position:absolute;top:270px;width:113px;height:113px;border-radius:50%;display:flex;align-items:center;justify-content:center;font-family:"Open Sans",sans-serif;font-weight:700;font-size:17px;color:var(--white);box-shadow:0 0 0 5px rgba(255,255,255,.18)}
.hero-arrow{position:absolute;top:258px;width:38px;height:38px;border-radius:50%;border:1px solid rgba(255,255,255,.35)}

/* sections */
.section-title{position:absolute;left:0;width:1200px;font-family:"Raleway",sans-serif;font-weight:700;font-size:19px;color:var(--navy)}
.lead{position:absolute;font-size:12px;line-height:25px;color:var(--muted)}
.service{position:absolute;top:876px;width:280px;text-align:center}
.service-icon{width:116px;height:116px;border-radius:50%;background:var(--navy);margin:0 auto;display:flex;align-items:center;justify-content:center}
.service-name{margin-top:30px;font-family:"Raleway",sans-serif;font-weight:700;font-size:13px;color:#333}
.service-text{margin-top:15px;font-size:12px;line-height:25px;color:var(--muted)}

.case{position:absolute;top:1288px;width:310px}
.case-photo{width:310px;height:195px}
.case-title{margin-top:21px;font-family:"Raleway",sans-serif;font-weight:700;font-size:15px;line-height:23px;color:#333}
.case-text{margin-top:11px;font-size:12px;line-height:24px;color:var(--muted)}

/* testimonial */
.testimonial{position:absolute;left:0;top:1709px;width:1200px;height:457px;background:linear-gradient(160deg,#1a2f3d 0%,#0d1e29 50%,#1c2f3a 100%)}
.quote-mark{position:absolute;left:0;width:1200px;top:78px;font-family:"Raleway",sans-serif;font-weight:700;font-size:64px;line-height:60px;color:var(--white)}
.quote-text{position:absolute;left:170px;width:860px;top:146px;font-size:13.5px;line-height:28px;color:var(--white)}
.avatar{position:absolute;left:552px;top:228px;width:96px;height:96px;border-radius:50%;border:4px solid var(--white);background:linear-gradient(#cfd6dc,#9aa6b0)}
.quote-author{position:absolute;left:0;width:1200px;top:342px;font-size:14px;color:var(--white)}
.quote-author b{font-weight:700}
.dots{position:absolute;left:586px;top:389px;display:flex;gap:6px}
.dots span{width:6px;height:6px;border-radius:50%;background:#4c6273}
.dots span.on{background:#8aa0b0}

/* footer */
.footer-col{position:absolute;top:2210px}
.footer-heading{font-family:"Raleway",sans-serif;font-weight:700;font-size:13px;color:var(--navy);margin-bottom:12px}
.footer-text{font-size:11.5px;line-height:22px;color:#555}
.footer-links{list-style:none;font-size:11.5px;line-height:22px;color:#555}
.btn{display:inline-block;margin-top:20px;width:112px;height:30px;line-height:30px;text-align:center;background:var(--navy);color:var(--white);font-size:9.5px;font-weight:700;border-radius:3px;letter-spacing:.3px}
.contact-row{display:flex;align-items:center;gap:8px}
.socials{display:flex;gap:8px;margin-top:18px}
.socials span{width:27px;height:27px;border-radius:50%;background:#c9c9c9}
.footer-brand{display:flex;align-items:center;gap:8px;margin-top:22px;font-family:"Raleway",sans-serif;font-weight:500;font-size:24px;color:#3a2a3a}
.footer-brand .brand-dot{width:24px;height:24px}
.footer-rule{position:absolute;left:100px;top:2427px;width:1000px;height:1px;background:var(--line)}
.copyright{position:absolute;left:0;width:1200px;top:2449px;font-size:11px;color:#666}
</style>
</head>
<body>

<header class="site-header">
  <div class="brand"><span class="brand-dot"></span>Quillbrookes</div>
  <nav class="main-nav">
    <span>HOME</span><span>FOUNDER</span><span>CONSULTANCY</span><span>SYSTEM</span><span>CASE STUDIES</span><span>CONTACT</span>
  </nav>
</header>

<section class="hero" role="img" aria-label="Photograph of planet Earth seen from space with glowing horizon">
  <h1 class="hero-title center">WORLD MERCHANDISING</h1>
  <p class="hero-sub center">WORLD MERCHANDISING TRADE 2012 ( USD BILLION)</p>
  <div class="bubble" style="left:311px;background:var(--blue)">0-250</div>
  <div class="bubble" style="left:465px;background:var(--green)">250-500</div>
  <div class="bubble" style="left:620px;background:var(--orange)">500-1000</div>
  <div class="bubble" style="left:775px;background:var(--red)">&gt;1000</div>
  <span class="hero-arrow" style="left:39px"></span>
  <span class="hero-arrow" style="left:1126px"></span>
</section>

<h2 class="section-title center" style="top:696px">WELCOME TO QUILL BROOKES</h2>
<p class="lead center" style="left:270px;width:660px;top:735px">Quillbrookes Consultancy Limited capitalizes on synergies arising from trade and investment linkages between countries and knowledge of traditional and non-traditional pools of liquidity to provide consultancy services to Emerging country banks, Corporates and SMEs.</p>

<div class="service" style="left:135px">
  <div class="service-icon">
    <svg width="56" height="56" viewBox="0 0 56 56" fill="none" stroke="#fff" stroke-width="2"><rect x="10" y="8" width="20" height="42"/><rect x="30" y="20" width="16" height="30"/><path d="M15 15h3M22 15h3M15 22h3M22 22h3M15 29h3M22 29h3M15 36h3M22 36h3M35 27h6M35 34h6M35 41h6M18 50v-6h4v6"/></svg>
  </div>
  <div class="service-name">FOUNDER</div>
  <p class="service-text">Ms. Meera Lastings is the founder director of Quillbrookes Consultancy Limited (QCL) based at Hong Kong.</p>
</div>
<div class="service" style="left:460px">
  <div class="service-icon">
    <svg width="60" height="56" viewBox="0 0 60 56" fill="none" stroke="#fff" stroke-width="2"><path d="M22 12h26a8 8 0 0 1 8 8v10a8 8 0 0 1-8 8h-2v7l-8-7H22"/><path d="M6 20a8 8 0 0 1 8-8h24a8 8 0 0 1 8 8v10a8 8 0 0 1-8 8H20l-9 8v-8a8 8 0 0 1-5-8z" fill="var(--navy)"/><circle cx="17" cy="25" r="3"/><circle cx="26" cy="25" r="3"/><circle cx="35" cy="25" r="3"/></svg>
  </div>
  <div class="service-name">CONSULTANCY</div>
  <p class="service-text">QCL will work with you to understand your business and offer need based strategic and transactional advice which fits...</p>
</div>
<div class="service" style="left:785px">
  <div class="service-icon">
    <svg width="58" height="58" viewBox="0 0 58 58" fill="none" stroke="#fff" stroke-width="2"><path d="M25 6h8l1 6 5 2 5-4 6 6-4 5 2 5 6 1v8l-6 1-2 5 4 5-6 6-5-4-5 2-1 6h-8l-1-6-5-2-5 4-6-6 4-5-2-5-6-1v-8l6-1 2-5-4-5 6-6 5 4 5-2z"/><circle cx="29" cy="29" r="9"/><circle cx="29" cy="29" r="3"/></svg>
  </div>
  <div class="service-name">SYSTEM</div>
  <p class="service-text">QCL will work with you to understand your business and offer need based strategic and transactional advice which fits...</p>
</div>

<h2 class="section-title center" style="top:1189px">CASE STUDIES</h2>
<p class="lead center" style="left:0;width:1200px;top:1229px">Some of the deals completed by QCL are summarised below to describe the range of activities undertaken with Corporates</p>

<article class="case" style="left:100px">
  <div class="case-photo" role="img" aria-label="Photo of glass office towers under a blue sky" style="background:linear-gradient(180deg,#4f8fd0 0%,#9cc3e6 50%,#5d6670 100%)"></div>
  <h3 class="case-title">Export Credit Agency backed long term financing</h3>
  <p class="case-text">Headquartered in Hong Kong, Group a has a vintage of over 100 years in the Diamond industry and a consolidated turnover of over USD</p>
</article>
<article class="case" style="left:445px">
  <div class="case-photo" role="img" aria-label="Photo of business people reviewing documents together" style="background:linear-gradient(135deg,#8a5a36 0%,#d8c2a4 45%,#eee7dc 70%,#b79a78 100%)"></div>
  <h3 class="case-title">Export Credit Agency backed long term financing</h3>
  <p class="case-text">Headquartered in Hong Kong, Group a has a vintage of over 100 years in the Diamond industry and a consolidated turnover of over USD</p>
</article>
<article class="case" style="left:791px">
  <div class="case-photo" role="img" aria-label="Photo of a businesswoman working at a laptop in a bright office" style="background:linear-gradient(135deg,#f2f4f6 0%,#dfe3e7 50%,#c8ced4 100%)"></div>
  <h3 class="case-title">Export Credit Agency backed long term financing</h3>
  <p class="case-text">Headquartered in Hong Kong, Group a has a vintage of over 100 years in the Diamond industry and a consolidated turnover of over USD</p>
</article>

<section class="testimonial" role="img" aria-label="Dark photo of a hand signing a document with a pen">
  <div class="quote-mark center">&ldquo;</div>
  <p class="quote-text center">Lorem Ipsum is simply dummy text of the printing and typesetting industry. Lorem Ipsum has been the industry's standard dummy text ever since the 1500s, when an unknown printer took a galley of type and scrambled it to make a type specimen book</p>
  <div class="avatar" role="img" aria-label="Portrait photo of the client"></div>
  <p class="quote-author center"><b>- Colin Maren -</b> Business man</p>
  <div class="dots"><span></span><span class="on"></span><span></span></div>
</section>

<footer>
  <div class="footer-col" style="left:100px;width:300px">
    <h4 class="footer-heading">ABOUT US</h4>
    <p class="footer-text">Quillbrookes Consultancy Limited capitalizes on synergies arising from trade and investment linkages between countries and knowledge of traditional and non-traditional pools of liquidity...</p>
    <span class="btn">READ MORE INFO</span>
  </div>
  <div class="footer-col" style="left:468px">
    <h4 class="footer-heading">WELCOME</h4>
    <ul class="footer-links"><li>Home</li><li>Founder</li><li>Consultancy</li><li>System</li><li>Case Studies</li><li>Contact</li><li>More</li></ul>
  </div>
  <div class="footer-col" style="left:647px;width:210px">
    <h4 class="footer-heading">CONTACT INFO</h4>
    <p class="footer-text">Unit 04, 9th Floor,<br>Harbourline Tower,<br>18 Linden Road, Kowloon<br>Hong Kong</p>
    <p class="footer-text contact-row"><svg width="11" height="11" viewBox="0 0 12 12"><path d="M2 1l2 0 1 3-1.5 1a6 6 0 0 0 3.5 3.5L8 7l3 1v2c0 1-1 1.5-2 1.5A9 9 0 0 1 .5 3C.5 2 1 1 2 1z" fill="var(--navy)"/></svg>+852-2100 4417</p>
    <p class="footer-text contact-row"><svg width="11" height="11" viewBox="0 0 12 12" fill="var(--navy)"><rect x="3" y="1" width="6" height="3"/><rect x="1" y="4" width="10" height="5" rx="1"/><rect x="3" y="7" width="6" height="4" fill="#fff" stroke="var(--navy)"/></svg>+852-2100 4418</p>
    <p class="footer-text contact-row"><svg width="11" height="9" viewBox="0 0 12 9"><rect width="12" height="9" fill="var(--navy)"/><path d="M0 0l6 5 6-5" stroke="#fff" fill="none"/></svg>query@quill-brookes.com</p>
  </div>
  <div class="footer-col" style="left:896px">
    <h4 class="footer-heading">FOLLOW US</h4>
    <p class="footer-text">Connect with our social network</p>
    <div class="socials"><span></span><span></span><span></span><span></span><span></span></div>
    <div class="footer-brand"><span class="brand-dot"></span>Quillbrookes</div>
  </div>
  <div class="footer-rule"></div>
  <p class="copyright center">© 2016, Quill brookes. All rights reserved</p>
</footer>

</body>
</html>
```